eCommerce website for a DIY shop & communal center

We need a website for a business called The Maple Bench. The Maple Bench is both a shop and communal establishment where people with shared interests, especially in DIY (Do It Yourself) and crafting, can gather to shop for & work on projects while sharing ideas, equipment, supplies and knowledge. The shop is both brick & motor and online. The physical communal space provides workstations, equipment, tools and supplies and expertise for DIY lovers to create their projects.

Target Market(s)

Middle & upper class DIY enthusiasts, creative hobbyists, budding artists & small business owners

Industry/Entity Type

DIY, Arts & Crafts

Coding

Coded - Design and coding required

Number of Pages Required

5+ page

Requirements
Must have
• Menus to include 1. home page (with about us, operating hours, contacts, location, meet the team); 2. Bench activities (how to DIY at the Bench, booking, equipment & tools, house rules); 3. Bench events (events in the Bench, offsite events); 4. Resources (FAQs, tutorials, blogs, eBooks) and 5. Online shop
Nice to have
• Branding guidelines eg logo colours (see attachment) to influence design. Tillpost shop. Booking feature for activities & events at the Bench.

```html
<!DOCTYPE html>
<html lang="en">
<head>
<meta charset="utf-8">
<title>The Maple Bench</title>
<link href="https://fonts.googleapis.com/css2?family=Work+Sans:wght@400;500;600;700;800&display=swap" rel="stylesheet">
<style>
:root{
  --blue:#1f3f8f;
  --ink:#1d1d1d;
  --text:#3a3a3a;
  --soft:#f4f0f0;
  --white:#ffffff;
  --line:#e2dede;
}
*{box-sizing:border-box;margin:0;padding:0}
html,body{width:1200px;height:4301px;overflow:hidden}
body{font-family:"Work Sans",Arial,sans-serif;color:var(--ink);background:var(--white);position:relative}
.abs{position:absolute}
.btn{position:absolute;background:var(--blue);color:var(--white);font-weight:700;font-size:12px;letter-spacing:.3px;display:flex;align-items:center;justify-content:center;text-transform:uppercase;white-space:nowrap}
.photo{position:absolute}

/* header */
.site-header{position:absolute;left:0;top:0;width:1200px;height:85px;background:var(--white)}
.logo{position:absolute;left:130px;top:28px;font-size:24px;font-weight:400;color:var(--ink);white-space:nowrap}
.nav a{position:absolute;top:35px;font-size:12.5px;font-weight:500;color:var(--ink);text-decoration:none;white-space:nowrap}
.cart-label{position:absolute;left:1003px;top:40px;font-size:9px;font-weight:500}
.cart-badge{position:absolute;left:1053px;top:27px;width:14px;height:14px;border-radius:50%;background:#2aa79b;color:#fff;font-size:9px;display:flex;align-items:center;justify-content:center}

/* hero */
.hero{position:absolute;left:0;top:85px;width:1200px;height:611px;background:linear-gradient(135deg,#f4d7e0 0%,#ece8e6 40%,#bfe6e2 70%,#d9eef0 100%)}
.hero-title{position:absolute;left:384px;top:288px;width:432px;height:52px;background:rgba(255,255,255,.85);font-size:35px;font-weight:800;text-align:center;line-height:52px;color:var(--ink);white-space:nowrap}
.hero-sub{position:absolute;left:267px;top:347px;width:668px;height:36px;background:rgba(255,255,255,.85);font-size:17px;text-align:center;line-height:36px;color:var(--ink);white-space:nowrap}
.dots{position:absolute;left:561px;top:646px;display:flex;gap:9px;align-items:center}
.dots span{width:6px;height:6px;border-radius:50%;background:#fff}
.dots span.on{width:10px;height:10px;border:2px solid #fff;background:var(--blue)}

/* section heads */
.sec-title{position:absolute;left:0;width:1200px;text-align:center;font-size:24px;font-weight:600;color:var(--ink)}
.sec-rule{position:absolute;left:568px;width:64px;height:3px;background:var(--blue)}

/* shop */
.product-name{position:absolute;width:297px;text-align:center;font-size:16px;font-weight:700}
.product-price{position:absolute;width:297px;text-align:center;font-size:17px;color:var(--text)}

/* events */
.events{position:absolute;left:0;top:1706px;width:1200px;height:601px;background:var(--soft)}
.event-card{position:absolute;top:137px;width:297px;height:414px;background:var(--white);box-shadow:0 1px 4px rgba(0,0,0,.08)}
.event-card .photo{left:0;top:0;width:297px;height:170px}
.event-date{position:absolute;left:25px;top:198px;font-size:12px;color:var(--text)}
.event-head{position:absolute;left:25px;top:222px;width:255px;font-size:13px;font-weight:500;line-height:23px;text-transform:uppercase;white-space:nowrap}
.event-body{position:absolute;left:25px;top:285px;width:250px;font-size:11px;line-height:17.5px;color:var(--text)}

/* team */
.team-card{position:absolute;top:2447px;width:297px;height:373px;background:var(--white);border:1px solid var(--line)}
.team-card .photo{left:0;top:0;width:295px;height:184px}
.team-name{position:absolute;left:0;top:210px;width:295px;text-align:center;font-size:16px;font-weight:500}
.team-body{position:absolute;left:30px;top:246px;width:235px;text-align:center;font-size:11px;line-height:17.5px;color:var(--text)}
.arrow{position:absolute;top:2619px}

/* blog */
.blog{position:absolute;left:0;top:2883px;width:1200px;height:601px;background:var(--soft)}
.post{position:absolute;overflow:hidden}
.post-shade{position:absolute;left:0;top:0;width:100%;height:100%}
.post-meta{position:absolute;left:14px;font-size:10.5px;color:#eee}
.post-head{position:absolute;left:14px;font-size:12.5px;font-weight:700;line-height:17px;color:#fff;text-transform:uppercase}
.post.big .post-meta{left:26px;top:279px;font-size:12px}
.post.big .post-head{left:26px;top:301px;font-size:18px;line-height:24px;width:380px}
.post-body{position:absolute;left:26px;top:355px;width:390px;font-size:11px;line-height:17px;color:#eee}

/* about */
.about-title{position:absolute;left:132px;top:3535px;font-size:26px;font-weight:700}
.about-rule{position:absolute;left:132px;top:3575px;width:96px;height:3px;background:var(--blue)}
.about-text{position:absolute;left:132px;top:3606px;width:400px;font-size:12.5px;line-height:20.8px;color:var(--text)}

/* footer */
.site-footer{position:absolute;left:0;top:3947px;width:1200px;height:354px;background:var(--blue)}
.foot-logo{position:absolute;left:130px;top:104px;font-size:30px;font-weight:400;color:#fff;white-space:nowrap}
.foot-head{position:absolute;top:52px;font-size:12px;font-weight:700;color:#fff}
.foot-links{position:absolute;left:452px;top:85px;list-style:none}
.foot-links li{font-size:11.5px;color:#fff;line-height:20px;text-transform:uppercase}
.foot-item{position:absolute;display:flex;align-items:flex-start;gap:12px;color:#fff;font-size:11.5px;line-height:15px;white-space:nowrap}
.foot-item .ic{width:24px;height:24px;border-radius:50%;background:#fff;flex:none;display:flex;align-items:center;justify-content:center}
.copyright{position:absolute;left:0;top:306px;width:1200px;text-align:center;font-size:9.5px;color:#dfe5f5}
</style>
</head>
<body>

<header class="site-header">
  <div class="logo">The Maple Bench</div>
  <nav class="nav">
    <a style="left:322px">HOME</a>
    <a style="left:391px">BENCH ACTIVITIES</a>
    <a style="left:548px">BENCH EVENTS</a>
    <a style="left:691px">RESOURCES</a>
    <a style="left:801px">ONLINE SHOP</a>
  </nav>
  <svg class="abs" style="left:960px;top:30px" width="26" height="26" viewBox="0 0 26 26"><circle cx="10.5" cy="10.5" r="7.5" fill="none" stroke="#222" stroke-width="3"/><line x1="16" y1="16" x2="23" y2="23" stroke="#222" stroke-width="3.5" stroke-linecap="round"/></svg>
  <div class="cart-label">CART</div>
  <svg class="abs" style="left:1030px;top:30px" width="30" height="28" viewBox="0 0 30 28"><path d="M1 3h5l4 15h15l3-11H8" fill="none" stroke="#222" stroke-width="2.5" stroke-linejoin="round"/><circle cx="12" cy="23" r="2.5" fill="#222"/><circle cx="23" cy="23" r="2.5" fill="#222"/></svg>
  <div class="cart-badge">0</div>
</header>

<section class="hero" role="img" aria-label="Pastel paper-roll bunny crafts scattered with jelly beans"></section>
<div class="hero-title">CRAFT BENCH WORKS</div>
<div class="hero-sub">Lorem Ipsum is simply dummy text of the printing and typesetting industry</div>
<div class="btn" style="left:526px;top:414px;width:148px;height:52px;font-size:19px">Shop Now</div>
<div class="dots"><span></span><span></span><span class="on"></span><span></span><span></span></div>

<!-- shop -->
<h2 class="sec-title" style="top:740px">SHOP</h2>
<div class="sec-rule" style="top:783px;left:580px;width:40px"></div>

<div class="photo" style="left:132px;top:828px;width:297px;height:274px;background:linear-gradient(135deg,#cfd3cc,#6e6552 60%,#d6b36a)" role="img" aria-label="Tin-can candle lanterns"></div>
<div class="photo" style="left:451px;top:828px;width:297px;height:274px;background:linear-gradient(135deg,#8b7a66,#d8d8d8 50%,#c5262c)" role="img" aria-label="String-art heart with red yarn"></div>
<div class="photo" style="left:770px;top:828px;width:297px;height:274px;background:linear-gradient(135deg,#3d4a55,#8c8c86 50%,#e8e2da)" role="img" aria-label="Decorated bottle vase with lace"></div>
<div class="product-name" style="left:132px;top:1125px">LOREM IPSUM</div>
<div class="product-name" style="left:451px;top:1125px">LOREM IPSUM</div>
<div class="product-name" style="left:770px;top:1125px">LOREM IPSUM</div>
<div class="product-price" style="left:132px;top:1153px">$15.99</div>
<div class="product-price" style="left:451px;top:1153px">$15.99</div>
<div class="product-price" style="left:770px;top:1153px">$15.99</div>
<div class="btn" style="left:234px;top:1189px;width:92px;height:30px">Shop Now</div>
<div class="btn" style="left:553px;top:1189px;width:92px;height:30px">Shop Now</div>
<div class="btn" style="left:872px;top:1189px;width:92px;height:30px">Shop Now</div>

<div class="photo" style="left:132px;top:1255px;width:297px;height:274px;background:linear-gradient(135deg,#d9a98a,#d8443a 45%,#7fae4f 70%,#e8c23a)" role="img" aria-label="Popsicle-stick photo frame"></div>
<div class="photo" style="left:451px;top:1255px;width:297px;height:274px;background:linear-gradient(135deg,#8a7a6e,#e8d0b0 50%,#554a40)" role="img" aria-label="Eggshell candles with dried flowers"></div>
<div class="photo" style="left:770px;top:1255px;width:297px;height:274px;background:linear-gradient(135deg,#e8c8d2,#b08898 50%,#ece8e8)" role="img" aria-label="Floral fabric sewing pattern"></div>
<div class="product-name" style="left:132px;top:1552px">LOREM IPSUM</div>
<div class="product-name" style="left:451px;top:1552px">LOREM IPSUM</div>
<div class="product-name" style="left:770px;top:1552px">LOREM IPSUM</div>
<div class="product-price" style="left:132px;top:1580px">$15.99</div>
<div class="product-price" style="left:451px;top:1580px">$15.99</div>
<div class="product-price" style="left:770px;top:1580px">$15.99</div>
<div class="btn" style="left:234px;top:1616px;width:92px;height:30px">Shop Now</div>
<div class="btn" style="left:553px;top:1616px;width:92px;height:30px">Shop Now</div>
<div class="btn" style="left:872px;top:1616px;width:92px;height:30px">Shop Now</div>

<!-- events -->
<section class="events">
  <h2 class="sec-title" style="top:45px">BENCH EVENTS</h2>
  <div class="sec-rule" style="top:94px"></div>

  <article class="event-card" style="left:132px">
    <div class="photo" style="background:linear-gradient(135deg,#c9a88a,#8a5a3c 55%,#e3c2a6)" role="img" aria-label="Hands crafting with fabric roll"></div>
    <div class="event-date">14 Sep, 2021</div>
    <div class="event-head">Lorem Ipsum is simply dum<br>my text of the printing</div>
    <div class="event-body">Sed ut perspiciatis unde omnis iste natus error sit voluptatem accusantium doloremque laudantium totam.</div>
    <div class="btn" style="left:27px;top:352px;width:90px;height:29px;font-size:11px">Read More</div>
  </article>
  <article class="event-card" style="left:451px">
    <div class="photo" style="background:linear-gradient(135deg,#6d6a5e,#e3e0d4 50%,#c94a55)" role="img" aria-label="Hands painting a craft project"></div>
    <div class="event-date">14 Sep, 2021</div>
    <div class="event-head">Lorem Ipsum is simply dum<br>my text of the printing</div>
    <div class="event-body">Sed ut perspiciatis unde omnis iste natus error sit voluptatem accusantium doloremque laudantium totam.</div>
    <div class="btn" style="left:27px;top:352px;width:90px;height:29px;font-size:11px">Read More</div>
  </article>
  <article class="event-card" style="left:770px">
    <div class="photo" style="background:linear-gradient(135deg,#c89a3c,#efe6d8 50%,#b89a78)" role="img" aria-label="Handmade paper flower decoration"></div>
    <div class="event-date">14 Sep, 2021</div>
    <div class="event-head">Lorem Ipsum is simply dum<br>my text of the printing</div>
    <div class="event-body">Sed ut perspiciatis unde omnis iste natus error sit voluptatem accusantium doloremque laudantium totam.</div>
    <div class="btn" style="left:27px;top:352px;width:90px;height:29px;font-size:11px">Read More</div>
  </article>
</section>

<!-- team -->
<h2 class="sec-title" style="top:2357px">MEET THE TEAM</h2>
<div class="sec-rule" style="top:2406px"></div>
<svg class="arrow" style="left:78px" width="16" height="24" viewBox="0 0 16 24"><path d="M12 3 4 12l8 9" fill="none" stroke="#999" stroke-width="2"/></svg>
<svg class="arrow" style="left:1097px" width="16" height="24" viewBox="0 0 16 24"><path d="M4 3l8 9-8 9" fill="none" stroke="#999" stroke-width="2"/></svg>

<article class="team-card" style="left:132px">
  <div class="photo" style="background:linear-gradient(135deg,#8a7a6a,#c8b8a8 50%,#5a7a9a)" role="img" aria-label="Portrait of team member Dorian"></div>
  <div class="team-name">DORIAN</div>
  <div class="team-body">Sed ut perspiciatis unde omnis iste natus error sit voluptatem accusantium doloremque laudantium totam.</div>
  <div class="btn" style="left:96px;top:311px;width:104px;height:30px;font-size:11px">View Profile</div>
</article>
<article class="team-card" style="left:452px">
  <div class="photo" style="background:linear-gradient(135deg,#eeeeee,#d9d9d9 50%,#6f98c8)" role="img" aria-label="Portrait of team member Owen Hale"></div>
  <div class="team-name">OWEN HALE</div>
  <div class="team-body">Sed ut perspiciatis unde omnis iste natus error sit voluptatem accusantium doloremque laudantium totam.</div>
  <div class="btn" style="left:96px;top:311px;width:104px;height:30px;font-size:11px">View Profile</div>
</article>
<article class="team-card" style="left:771px">
  <div class="photo" style="background:linear-gradient(135deg,#4a9aa8,#c9d8d6 50%,#2f4a35)" role="img" aria-label="Portrait of team member Tomas Reyes"></div>
  <div class="team-name">TOMAS REYES</div>
  <div class="team-body">Sed ut perspiciatis unde omnis iste natus error sit voluptatem accusantium doloremque laudantium totam.</div>
  <div class="btn" style="left:96px;top:311px;width:104px;height:30px;font-size:11px">View Profile</div>
</article>

<!-- blog -->
<section class="blog">
  <h2 class="sec-title" style="top:45px">LATEST BLOG</h2>
  <div class="sec-rule" style="top:94px"></div>

  <article class="post big" style="left:132px;top:139px;width:447px;height:400px;background:linear-gradient(160deg,#5d6a4a,#c44a7a 45%,#2a2a2a)" role="img" aria-label="Succulents in pink pots">
    <div class="post-shade" style="background:linear-gradient(180deg,rgba(0,0,0,0) 40%,rgba(0,0,0,.7))"></div>
    <div class="post-meta">14 Sep, 2021</div>
    <div class="post-head">Lorem Ipsum is simply dummy<br>text of the printing</div>
    <div class="post-body">Sed ut perspiciatis unde omnis iste natus error sit voluptatem accusantium doloremque laudantium totam.</div>
  </article>

  <article class="post" style="left:594px;top:139px;width:227px;height:193px;background:linear-gradient(135deg,#e0d6cc,#b8283a 50%,#3a2a2a)" role="img" aria-label="Hands painting a red mask">
    <div class="post-shade" style="background:linear-gradient(180deg,rgba(0,0,0,0) 30%,rgba(0,0,0,.75))"></div>
    <div class="post-meta" style="top:106px">14 Sep, 2021</div>
    <div class="post-head" style="top:124px;width:205px">Lorem Ipsum is simply dummy text of the printing</div>
  </article>
  <article class="post" style="left:840px;top:139px;width:227px;height:193px;background:linear-gradient(135deg,#6a5a4a,#e8e4e0 50%,#2a2a2a)" role="img" aria-label="Painted skull decoration">
    <div class="post-shade" style="background:linear-gradient(180deg,rgba(0,0,0,0) 30%,rgba(0,0,0,.75))"></div>
    <div class="post-meta" style="top:106px">14 Sep, 2021</div>
    <div class="post-head" style="top:124px;width:205px">Lorem Ipsum is simply dummy text of the printing</div>
  </article>
  <article class="post" style="left:594px;top:348px;width:227px;height:193px;background:linear-gradient(135deg,#d8c0b0,#f0d8d0 50%,#5a4a4a)" role="img" aria-label="Knitted pink hearts">
    <div class="post-shade" style="background:linear-gradient(180deg,rgba(0,0,0,0) 30%,rgba(0,0,0,.75))"></div>
    <div class="post-meta" style="top:106px">14 Sep, 2021</div>
    <div class="post-head" style="top:124px;width:205px">Lorem Ipsum is simply dummy text of the printing</div>
  </article>
  <article class="post" style="left:840px;top:348px;width:227px;height:193px;background:linear-gradient(135deg,#9a7ac0,#f0e0d8 50%,#6a4a6a)" role="img" aria-label="Eggshell candle with lilac flowers">
    <div class="post-shade" style="background:linear-gradient(180deg,rgba(0,0,0,0) 30%,rgba(0,0,0,.75))"></div>
    <div class="post-meta" style="top:106px">14 Sep, 2021</div>
    <div class="post-head" style="top:124px;width:205px">Lorem Ipsum is simply dummy text of the printing</div>
  </article>
</section>

<!-- about -->
<h2 class="about-title">ABOUT US</h2>
<div class="about-rule"></div>
<p class="about-text">But I must explain to you how all this mistaken idea of denouncing pleasure and praising pain was born and I will give you a complete account of the system, and expound the actual teachings of the great explorer of the truth, the master-builder of human happiness. No one rejects, dislikes, or avoids pleasure itself, because it is pleasure, but because those who do not know how to pursue pleasure rationally encounter consequences that are extremely painful. Nor again is there anyone who loves or pursues or desires to obtain pain of itself, because it is pain.</p>
<div class="btn" style="left:132px;top:3841px;width:95px;height:32px;font-size:11px">Read More</div>
<div class="photo" style="left:584px;top:3484px;width:616px;height:463px;background:linear-gradient(135deg,#2e7a6a,#f4b8c0 35%,#f08898 55%,#e8d8e0 80%,#7a4a8a)" role="img" aria-label="Crafting table with pencils, scissors, pegs and glue gun"></div>

<!-- footer -->
<footer class="site-footer">
  <div class="foot-logo">The Maple Bench</div>

  <div class="foot-head" style="left:452px">MENU</div>
  <ul class="foot-links">
    <li>Home</li><li>Bench Activities</li><li>Bench Events</li><li>Resources</li><li>Online Shop</li>
  </ul>

  <div class="foot-head" style="left:673px">CONTACT US</div>
  <div class="foot-item" style="left:670px;top:86px">
    <span class="ic"><svg width="12" height="14" viewBox="0 0 12 14"><path d="M6 1a4.5 4.5 0 0 0-4.5 4.5C1.5 9 6 13 6 13s4.5-4 4.5-7.5A4.5 4.5 0 0 0 6 1z" fill="#1f3f8f"/><circle cx="6" cy="5.5" r="1.6" fill="#fff"/></svg></span>
    <span>512 Alder Lane<br>Brookfield, OR 97000</span>
  </div>
  <div class="foot-item" style="left:670px;top:136px">
    <span class="ic"><svg width="12" height="12" viewBox="0 0 12 12"><path d="M2.5 1h2l1 3-1.5 1a6 6 0 0 0 3 3l1-1.5 3 1v2c0 .6-.4 1-1 1C5 11 1 7 1 2c0-.6.4-1 1-1z" fill="#1f3f8f"/></svg></span>
    <span>Call Us<br>555.014.2290</span>
  </div>
  <div class="foot-item" style="left:670px;top:186px">
    <span class="ic"><svg width="12" height="10" viewBox="0 0 12 10"><rect x="0.5" y="0.5" width="11" height="9" fill="#1f3f8f"/><path d="M1 1l5 4 5-4" fill="none" stroke="#fff" stroke-width="1.2"/></svg></span>
    <span>E mail Us<br>hello@maplebench.example</span>
  </div>

  <div class="foot-head" style="left:963px">FOLLOW US</div>
  <div class="foot-item" style="left:961px;top:86px"><span class="ic"></span><span>Like us on<br>FRIENDWALL</span></div>
  <div class="foot-item" style="left:961px;top:136px"><span class="ic"></span><span>Follow us on<br>CHIRPER</span></div>
  <div class="foot-item" style="left:961px;top:186px"><span class="ic"></span><span>Follow us on<br>WORKNET</span></div>

  <div class="copyright">Copyright © 2021 All Rights Reserved</div>
</footer>

</body>
</html>
```